1" x 3" label needed for essential oil bottle(s) - new ecommerce company

We need a label designed for 10 ml bottles of essential oils. We are offering 9 different types of essential oil: Lavender, Cedarwood, Eucalyptus, Frankincense, Lemon, Orange, Peppermint, Rosemary, and Tea Tree. The label should have a space for the type of essential oil. The bottles are an amber color (am including a photo) as essential oils are sensitive to light. also am including an AI file of our logo, which we'd like included on the label; the logo file also contains our logo colors, a dark blue and light grey. We'd also like the following on the label: "CAUTION: EYE AND SKIN IRRITANT. Avoid contact with eyes and skin. Wash hands after handling. If eye contact occurs, flush with water for 15 minutes. Not intended for topical or internal use. Contains Essential Oils. KEEP OUT OF REACH OF CHILDREN."
Also "Ingredients: 100% pure essential oil, GC tested."
Also "0.33 fl oz (10 ml)
Finally, we will need to include a sideways bar code on the right side of the label, so need 3/8" of white space on the right of the label.
We'd like the label to be calming, but modern, friendly, and confident.

```html
<!DOCTYPE html>
<html lang="en">
<head>
<meta charset="utf-8">
<title>Solvera Essential Oil Labels</title>
<link rel="stylesheet" href="https://fonts.googleapis.com/css2?family=Cormorant+Garamond:wght@500;600;700&family=Lora:wght@500&display=swap">
<style>
  :root {
    --canvas: #f3f3f2;
    --ink-light: #ffffff;
    --barcode-space: #ffffff;
    --cedarwood: #c4643a;
    --eucalyptus: #34444e;
    --frankincense: #bf9a6e;
    --rosemary: #c89b8d;
    --tea-tree: #aaa59d;
    --peppermint: #9fbe9c;
    --lemon: #dcc27c;
    --orange: #eda577;
    --lavender: #aeabd6;
  }
  * { box-sizing: border-box; margin: 0; padding: 0; }
  html, body {
    width: 1200px;
    height: 556px;
    overflow: hidden;
    background: var(--canvas);
  }
  .label-row {
    width: 1200px;
    height: 556px;
    display: flex;
    justify-content: center;
    align-items: center;
    gap: 13px;
  }
  .label {
    width: 114px;
    height: 206px;
    display: flex;
    color: var(--ink-light);
    font-variant-numeric: lining-nums;
  }
  .label-face {
    flex: 1;
    display: flex;
    flex-direction: column;
    align-items: center;
    padding: 12px 5px 7px;
    min-width: 0;
  }
  .barcode-space {
    width: 14px;
    flex: none;
    background: var(--barcode-space);
  }
  .label--cedarwood { background: var(--cedarwood); }
  .label--eucalyptus { background: var(--eucalyptus); }
  .label--frankincense { background: var(--frankincense); }
  .label--rosemary { background: var(--rosemary); }
  .label--tea-tree { background: var(--tea-tree); }
  .label--peppermint { background: var(--peppermint); }
  .label--lemon { background: var(--lemon); }
  .label--orange { background: var(--orange); }
  .label--lavender { background: var(--lavender); }

  .brand {
    display: flex;
    align-items: center;
    gap: 3px;
    align-self: stretch;
  }
  .brand-dot {
    width: 9px;
    height: 9px;
    border: 1px solid currentColor;
    border-radius: 50%;
    opacity: 0.7;
    flex: none;
  }
  .brand-text { display: flex; flex-direction: column; align-items: center; flex: 1; }
  .brand-name {
    font-family: "Cormorant Garamond", serif;
    font-weight: 600;
    font-size: 10px;
    letter-spacing: 1.8px;
    line-height: 1;
  }
  .brand-tagline {
    font-family: "Cormorant Garamond", serif;
    font-weight: 700;
    font-size: 4px;
    letter-spacing: 0.3px;
    margin-top: 2px;
    white-space: nowrap;
  }
  .rule {
    align-self: stretch;
    height: 1px;
    background: currentColor;
    opacity: 0.55;
    margin-top: 6px;
  }
  .accent {
    align-self: flex-start;
    margin-top: 4px;
    font-family: "Cormorant Garamond", serif;
    font-size: 7px;
    line-height: 1;
  }
  .oil-name {
    font-family: "Lora", serif;
    font-weight: 500;
    font-size: 12px;
    margin-top: 6px;
    white-space: nowrap;
  }
  .purity {
    font-family: "Cormorant Garamond", serif;
    font-weight: 700;
    font-size: 5px;
    letter-spacing: 0.4px;
    margin-top: 8px;
    padding-bottom: 2px;
    border-bottom: 0.5px solid currentColor;
    white-space: nowrap;
  }
  .ingredients {
    font-family: "Cormorant Garamond", serif;
    font-weight: 700;
    font-size: 4.4px;
    margin-top: 6px;
    text-align: center;
    white-space: nowrap;
  }
  .caution {
    font-family: "Cormorant Garamond", serif;
    font-weight: 700;
    font-size: 4.2px;
    line-height: 1.25;
    text-align: center;
    margin-top: 5px;
  }
  .caution strong { letter-spacing: 0.2px; }
  .volume {
    font-family: "Cormorant Garamond", serif;
    font-weight: 700;
    font-size: 5.5px;
    margin-top: auto;
    white-space: nowrap;
  }
  .volume-dot {
    display: inline-block;
    width: 2.5px;
    height: 2.5px;
    border-radius: 50%;
    background: currentColor;
    margin: 0 1px 0.5px;
  }
</style>
</head>
<body>
<main class="label-row">
  <section class="label label--cedarwood">
    <div class="label-face">
      <div class="brand"><span class="brand-dot"></span><div class="brand-text"><span class="brand-name">SOLVERA</span><span class="brand-tagline">CALM THAT GLOWS WITHIN</span></div></div>
      <div class="rule"></div><span class="accent">+</span>
      <h2 class="oil-name">Cedarwood</h2>
      <p class="purity">100% PURE ESSENTIAL OIL</p>
      <p class="ingredients">Ingredients: 100% pure essential oil, GC tested.</p>
      <p class="caution"><strong>CAUTION: EYE AND SKIN IRRITANT.</strong> Avoid contact with eyes and skin. Wash hands after handling. If eye contact occurs, flush with water for 15 minutes. Not intended for topical or internal use. Contains Essential Oils. <strong>KEEP OUT OF REACH OF CHILDREN.</strong></p>
      <p class="volume">0.33 fl oz <span class="volume-dot"></span> (10 ml)</p>
    </div>
    <div class="barcode-space"></div>
  </section>
  <section class="label label--eucalyptus">
    <div class="label-face">
      <div class="brand"><span class="brand-dot"></span><div class="brand-text"><span class="brand-name">SOLVERA</span><span class="brand-tagline">CALM THAT GLOWS WITHIN</span></div></div>
      <div class="rule"></div><span class="accent">+</span>
      <h2 class="oil-name">Eucalyptus</h2>
      <p class="purity">100% PURE ESSENTIAL OIL</p>
      <p class="ingredients">Ingredients: 100% pure essential oil, GC tested.</p>
      <p class="caution"><strong>CAUTION: EYE AND SKIN IRRITANT.</strong> Avoid contact with eyes and skin. Wash hands after handling. If eye contact occurs, flush with water for 15 minutes. Not intended for topical or internal use. Contains Essential Oils. <strong>KEEP OUT OF REACH OF CHILDREN.</strong></p>
      <p class="volume">0.33 fl oz <span class="volume-dot"></span> (10 ml)</p>
    </div>
    <div class="barcode-space"></div>
  </section>
  <section class="label label--frankincense">
    <div class="label-face">
      <div class="brand"><span class="brand-dot"></span><div class="brand-text"><span class="brand-name">SOLVERA</span><span class="brand-tagline">CALM THAT GLOWS WITHIN</span></div></div>
      <div class="rule"></div><span class="accent">+</span>
      <h2 class="oil-name">Frankincense</h2>
      <p class="purity">100% PURE ESSENTIAL OIL</p>
      <p class="ingredients">Ingredients: 100% pure essential oil, GC tested.</p>
      <p class="caution"><strong>CAUTION: EYE AND SKIN IRRITANT.</strong> Avoid contact with eyes and skin. Wash hands after handling. If eye contact occurs, flush with water for 15 minutes. Not intended for topical or internal use. Contains Essential Oils. <strong>KEEP OUT OF REACH OF CHILDREN.</strong></p>
      <p class="volume">0.33 fl oz <span class="volume-dot"></span> (10 ml)</p>
    </div>
    <div class="barcode-space"></div>
  </section>
  <section class="label label--rosemary">
    <div class="label-face">
      <div class="brand"><span class="brand-dot"></span><div class="brand-text"><span class="brand-name">SOLVERA</span><span class="brand-tagline">CALM THAT GLOWS WITHIN</span></div></div>
      <div class="rule"></div><span class="accent">+</span>
      <h2 class="oil-name">Rosemary</h2>
      <p class="purity">100% PURE ESSENTIAL OIL</p>
      <p class="ingredients">Ingredients: 100% pure essential oil, GC tested.</p>
      <p class="caution"><strong>CAUTION: EYE AND SKIN IRRITANT.</strong> Avoid contact with eyes and skin. Wash hands after handling. If eye contact occurs, flush with water for 15 minutes. Not intended for topical or internal use. Contains Essential Oils. <strong>KEEP OUT OF REACH OF CHILDREN.</strong></p>
      <p class="volume">0.33 fl oz <span class="volume-dot"></span> (10 ml)</p>
    </div>
    <div class="barcode-space"></div>
  </section>
  <section class="label label--tea-tree">
    <div class="label-face">
      <div class="brand"><span class="brand-dot"></span><div class="brand-text"><span class="brand-name">SOLVERA</span><span class="brand-tagline">CALM THAT GLOWS WITHIN</span></div></div>
      <div class="rule"></div><span class="accent">+</span>
      <h2 class="oil-name">Tea Tree</h2>
      <p class="purity">100% PURE ESSENTIAL OIL</p>
      <p class="ingredients">Ingredients: 100% pure essential oil, GC tested.</p>
      <p class="caution"><strong>CAUTION: EYE AND SKIN IRRITANT.</strong> Avoid contact with eyes and skin. Wash hands after handling. If eye contact occurs, flush with water for 15 minutes. Not intended for topical or internal use. Contains Essential Oils. <strong>KEEP OUT OF REACH OF CHILDREN.</strong></p>
      <p class="volume">0.33 fl oz <span class="volume-dot"></span> (10 ml)</p>
    </div>
    <div class="barcode-space"></div>
  </section>
  <section class="label label--peppermint">
    <div class="label-face">
      <div class="brand"><span class="brand-dot"></span><div class="brand-text"><span class="brand-name">SOLVERA</span><span class="brand-tagline">CALM THAT GLOWS WITHIN</span></div></div>
      <div class="rule"></div><span class="accent">+</span>
      <h2 class="oil-name">Peppermint</h2>
      <p class="purity">100% PURE ESSENTIAL OIL</p>
      <p class="ingredients">Ingredients: 100% pure essential oil, GC tested.</p>
      <p class="caution"><strong>CAUTION: EYE AND SKIN IRRITANT.</strong> Avoid contact with eyes and skin. Wash hands after handling. If eye contact occurs, flush with water for 15 minutes. Not intended for topical or internal use. Contains Essential Oils. <strong>KEEP OUT OF REACH OF CHILDREN.</strong></p>
      <p class="volume">0.33 fl oz <span class="volume-dot"></span> (10 ml)</p>
    </div>
    <div class="barcode-space"></div>
  </section>
  <section class="label label--lemon">
    <div class="label-face">
      <div class="brand"><span class="brand-dot"></span><div class="brand-text"><span class="brand-name">SOLVERA</span><span class="brand-tagline">CALM THAT GLOWS WITHIN</span></div></div>
      <div class="rule"></div><span class="accent">+</span>
      <h2 class="oil-name">Lemon</h2>
      <p class="purity">100% PURE ESSENTIAL OIL</p>
      <p class="ingredients">Ingredients: 100% pure essential oil, GC tested.</p>
      <p class="caution"><strong>CAUTION: EYE AND SKIN IRRITANT.</strong> Avoid contact with eyes and skin. Wash hands after handling. If eye contact occurs, flush with water for 15 minutes. Not intended for topical or internal use. Contains Essential Oils. <strong>KEEP OUT OF REACH OF CHILDREN.</strong></p>
      <p class="volume">0.33 fl oz <span class="volume-dot"></span> (10 ml)</p>
    </div>
    <div class="barcode-space"></div>
  </section>
  <section class="label label--orange">
    <div class="label-face">
      <div class="brand"><span class="brand-dot"></span><div class="brand-text"><span class="brand-name">SOLVERA</span><span class="brand-tagline">CALM THAT GLOWS WITHIN</span></div></div>
      <div class="rule"></div><span class="accent">+</span>
      <h2 class="oil-name">Orange</h2>
      <p class="purity">100% PURE ESSENTIAL OIL</p>
      <p class="ingredients">Ingredients: 100% pure essential oil, GC tested.</p>
      <p class="caution"><strong>CAUTION: EYE AND SKIN IRRITANT.</strong> Avoid contact with eyes and skin. Wash hands after handling. If eye contact occurs, flush with water for 15 minutes. Not intended for topical or internal use. Contains Essential Oils. <strong>KEEP OUT OF REACH OF CHILDREN.</strong></p>
      <p class="volume">0.33 fl oz <span class="volume-dot"></span> (10 ml)</p>
    </div>
    <div class="barcode-space"></div>
  </section>
  <section class="label label--lavender">
    <div class="label-face">
      <div class="brand"><span class="brand-dot"></span><div class="brand-text"><span class="brand-name">SOLVERA</span><span class="brand-tagline">CALM THAT GLOWS WITHIN</span></div></div>
      <div class="rule"></div><span class="accent">+</span>
      <h2 class="oil-name">Lavender</h2>
      <p class="purity">100% PURE ESSENTIAL OIL</p>
      <p class="ingredients">Ingredients: 100% pure essential oil, GC tested.</p>
      <p class="caution"><strong>CAUTION: EYE AND SKIN IRRITANT.</strong> Avoid contact with eyes and skin. Wash hands after handling. If eye contact occurs, flush with water for 15 minutes. Not intended for topical or internal use. Contains Essential Oils. <strong>KEEP OUT OF REACH OF CHILDREN.</strong></p>
      <p class="volume">0.33 fl oz <span class="volume-dot"></span> (10 ml)</p>
    </div>
    <div class="barcode-space"></div>
  </section>
</main>
</body>
</html>
```